Tallon Electrical Business Card

We need a business card design for our family-run electrical contracting business based in Western Australia called 'Tallon Electrical'. We provide electrical services including residential, commercial and industrial. We aim for individual business cards to be made for all of our employees. We already have a company logo, which we require to be featured on the design. We would like simple, sleek and vibrant designs, which incorporate our logo and represent our business. We do not want anything involving too many graphics/images. We like the colours red, black, white and all shades of grey. The final design should communicate professionalism and trustworthiness.
We require the following contact information:
Name- Grant Pellow
EC 5871
Mobile number- 0455 870 219
Fax number (including area code)- (08) 9560 2831
Email adress- name@tallonelectrical.com.au
Electrical
- ITC Handel Bold

```html
<!DOCTYPE html>
<html lang="en">
<head>
<meta charset="utf-8">
<title>Tallon Electrical Business Card</title>
<link rel="stylesheet" href="https://fonts.googleapis.com/css2?family=Michroma&family=Arimo:wght@400;700&display=swap">
<style>
  :root {
    --red: #d7131b;
    --black: #141414;
    --white: #f4f4f2;
    --grey-bg: #9a9a9a;
    --grey-text: #3c3c3c;
    --rule: #8a8a8a;
  }
  * { box-sizing: border-box; margin: 0; padding: 0; }
  html, body { width: 1200px; height: 720px; overflow: hidden; }
  body {
    background: var(--grey-bg);
    font-family: "Arimo", Arial, sans-serif;
    position: relative;
  }
  .card {
    position: absolute;
    top: 205px;
    width: 540px;
    height: 309px;
    background: var(--white);
    box-shadow: 0 6px 18px rgba(0,0,0,0.25);
    overflow: hidden;
  }
  .card--front { left: 40px; }
  .card--back { left: 620px; }

  .wordmark {
    display: flex;
    align-items: center;
    gap: 10px;
    font-family: "Michroma", sans-serif;
    font-size: 22px;
    letter-spacing: 1px;
    white-space: nowrap;
  }
  .wordmark__mark { width: 14px; height: 14px; background: var(--red); flex: none; }

  .card--front .wordmark {
    position: absolute;
    top: 108px; left: 0; right: 0;
    justify-content: center;
    color: var(--black);
  }
  .services {
    position: absolute;
    top: 162px; left: 0; right: 0;
    text-align: center;
    font-weight: 700;
    font-size: 13px;
    letter-spacing: 0.6px;
    color: var(--red);
  }
  .services .divider { color: var(--black); font-weight: 400; padding: 0 4px; }

  .band {
    position: absolute;
    top: 0; left: 0; right: 0;
    height: 118px;
    background: var(--black);
  }
  .card--back .wordmark {
    position: absolute;
    top: 46px; left: 36px;
    color: var(--white);
    font-size: 20px;
  }
  .rule {
    position: absolute;
    top: 142px; left: 30px; right: 30px;
    height: 1px;
    background: var(--rule);
  }
  .address {
    position: absolute;
    top: 152px; left: 30px;
    display: flex; gap: 8px;
    font-size: 14px;
    line-height: 17px;
    color: var(--grey-text);
  }
  .address svg { margin-top: 2px; flex: none; }

  .contact {
    position: absolute;
    right: 30px; bottom: 20px;
    text-align: right;
    color: var(--grey-text);
    font-size: 14px;
    line-height: 18px;
  }
  .contact__name { color: var(--red); font-weight: 700; font-size: 16px; line-height: 19px; }
  .contact__title { margin-bottom: 6px; }
  .contact__row { display: flex; justify-content: flex-end; align-items: center; gap: 8px; }
  .contact__row svg { flex: none; }
</style>
</head>
<body>

<section class="card card--front" aria-label="Business card front">
  <div class="wordmark"><span class="wordmark__mark"></span><span>TALLON ELECTRICAL</span></div>
  <p class="services">Residential<span class="divider">|</span>Industrial<span class="divider">|</span>Commercial</p>
</section>

<section class="card card--back" aria-label="Business card back">
  <div class="band"></div>
  <div class="wordmark"><span class="wordmark__mark"></span><span>TALLON ELECTRICAL</span></div>
  <div class="rule"></div>

  <div class="address">
    <svg width="10" height="14" viewBox="0 0 10 14" aria-hidden="true">
      <path d="M5 0a5 5 0 0 0-5 5c0 4 5 9 5 9s5-5 5-9a5 5 0 0 0-5-5z" fill="var(--red)"/>
      <circle cx="5" cy="5" r="1.8" fill="var(--white)"/>
    </svg>
    <p>EC 5871, address<br>town here 6542U</p>
  </div>

  <div class="contact">
    <p class="contact__name">Grant Pellow</p>
    <p class="contact__title">Director</p>
    <p class="contact__row"><span>0455 870 219</span>
      <svg width="12" height="12" viewBox="0 0 12 12" aria-label="Mobile"><rect x="1" y="1" width="10" height="10" fill="none" stroke="var(--red)" stroke-width="1.5"/></svg>
    </p>
    <p class="contact__row"><span>(08) 9560 2831</span>
      <svg width="12" height="12" viewBox="0 0 12 12" aria-label="Fax"><rect x="3" y="0.5" width="6" height="3" fill="var(--red)"/><rect x="0.5" y="4" width="11" height="5" fill="var(--red)"/><rect x="3" y="8" width="6" height="3.5" fill="var(--white)" stroke="var(--red)"/></svg>
    </p>
    <p class="contact__row"><span>name@tallonelectrical.com.au</span>
      <svg width="12" height="12" viewBox="0 0 12 12" aria-label="Email"><rect x="0.5" y="2.5" width="11" height="8" fill="var(--red)"/><path d="M0.5 2.5 6 7l5.5-4.5" fill="none" stroke="var(--white)" stroke-width="1"/></svg>
    </p>
  </div>
</section>

</body>
</html>
```